Business card por a urban DJ, up scale audience target

Need a sober design, modern, conservative colors but i can consider some options, y play rnb, hip hop, EDM and top40.

Business card for contact and personal info, double sided, use logo attrached please; im 42 so i need a card acording to my age an target audience.

Target Market(s)

Adult people, up scale audience

Industry/Entity Type

Music Download

Contact Information for Business Card

Cel (318) 4207265518 www.lumadrift.com

Requirements
Must have
• open mind
Nice to have
• open mind
Should not have
• DJ

```html
<!DOCTYPE html>
<html lang="en">
<head>
<meta charset="utf-8">
<title>Business Card – Luma</title>
<link rel="stylesheet" href="https://fonts.googleapis.com/css2?family=Open+Sans:wght@400;700&display=swap">
<style>
  :root {
    --page-bg: #d8d4ce;
    --card-dark: #3a3532;
    --card-light: #f1efec;
    --card-light-edge: #dcd8d3;
    --ink: #3c3835;
    --ink-soft: #4a4542;
    --icon-fg: #f1efec;
  }
  * { margin: 0; padding: 0; box-sizing: border-box; }
  html, body {
    width: 1200px;
    height: 970px;
    overflow: hidden;
    background: var(--page-bg);
    font-family: "Open Sans", Arial, sans-serif;
  }
  .card {
    position: absolute;
    left: 100px;
    top: 200px;
    width: 1000px;
    height: 570px;
    overflow: hidden;
    box-shadow: 0 18px 40px rgba(0,0,0,0.22);
  }
  .card-art {
    position: absolute;
    inset: 0;
    width: 100%;
    height: 100%;
  }
  .brand {
    position: absolute;
    left: 600px;
    top: 58px;
    display: flex;
    align-items: center;
    gap: 18px;
    color: var(--card-dark);
    font-weight: 700;
    font-size: 104px;
    letter-spacing: 4px;
    line-height: 1;
  }
  .brand-square {
    width: 34px;
    height: 34px;
    background: var(--card-dark);
  }
  .holder {
    position: absolute;
    left: 62px;
    top: 255px;
    color: var(--ink);
  }
  .holder-name {
    font-weight: 700;
    font-size: 33px;
    letter-spacing: 0.5px;
    line-height: 1.1;
  }
  .holder-role {
    font-size: 22px;
    color: var(--ink-soft);
    line-height: 1.3;
  }
  .contacts {
    position: absolute;
    left: 64px;
    top: 385px;
    list-style: none;
    color: var(--ink);
    font-size: 25px;
  }
  .contact {
    display: flex;
    align-items: center;
    gap: 12px;
    height: 35px;
  }
  .contact-icon {
    width: 22px;
    height: 22px;
    flex: none;
  }
</style>
</head>
<body>
  <section class="card" aria-label="Business card, front">
    <svg class="card-art" viewBox="0 0 1000 570" preserveAspectRatio="none" aria-hidden="true">
      <defs>
        <linearGradient id="frost" x1="0" y1="0" x2="1" y2="1">
          <stop offset="0" stop-color="var(--card-light)"/>
          <stop offset="0.6" stop-color="#f6f5f3"/>
          <stop offset="1" stop-color="var(--card-light-edge)"/>
        </linearGradient>
      </defs>
      <rect width="1000" height="570" fill="var(--card-dark)"/>
      <path d="M0,250 C220,80 620,18 1000,8 L1000,240 C820,470 420,545 0,545 Z" fill="url(#frost)"/>
    </svg>

    <div class="brand"><span>LUMA</span><span class="brand-square"></span></div>

    <div class="holder">
      <p class="holder-name">EMPLOYEE NAME</p>
      <p class="holder-role">Development Manager</p>
    </div>

    <ul class="contacts">
      <li class="contact">
        <svg class="contact-icon" viewBox="0 0 22 22" aria-hidden="true">
          <rect width="22" height="22" fill="var(--card-dark)"/>
          <rect x="7" y="3" width="8" height="16" rx="1.5" fill="none" stroke="var(--icon-fg)" stroke-width="1.6"/>
          <rect x="9" y="5.5" width="4" height="4" fill="var(--icon-fg)"/>
        </svg>
        <span>(318) 4207265518</span>
      </li>
      <li class="contact">
        <svg class="contact-icon" viewBox="0 0 22 22" aria-hidden="true">
          <rect width="22" height="22" fill="var(--card-dark)"/>
          <rect x="4" y="6" width="14" height="10" fill="none" stroke="var(--icon-fg)" stroke-width="1.5"/>
          <path d="M4,6 L11,12 L18,6" fill="none" stroke="var(--icon-fg)" stroke-width="1.5"/>
        </svg>
        <span>hello@lumadrift.com</span>
      </li>
      <li class="contact">
        <svg class="contact-icon" viewBox="0 0 22 22" aria-hidden="true">
          <rect width="22" height="22" rx="11" fill="var(--card-dark)"/>
          <circle cx="11" cy="11" r="7" fill="none" stroke="var(--icon-fg)" stroke-width="1.3"/>
          <ellipse cx="11" cy="11" rx="3" ry="7" fill="none" stroke="var(--icon-fg)" stroke-width="1.1"/>
          <path d="M4,11 H18 M5.5,7.5 H16.5 M5.5,14.5 H16.5" stroke="var(--icon-fg)" stroke-width="1.1"/>
        </svg>
        <span>www.lumadrift.com</span>
      </li>
    </ul>
  </section>
</body>
</html>
```